Kelvara Pools

Luxury pool designer builder brochure

Company name is "Kelvara"
Tag line is "Pools for the Mind Body & Soul"
Maybe integrate "Luxury Urban Lifestyle"

Target Market(s)

30 to 65 income of 200000.00 plus Affluent, high end life style
Luxury living

Industry/Entity Type

It Company

Font styles to use
Serif

Colors
000000

Requirements
Must have
• NOTE:
• Please remove the "Aquatic environments for the under the logo.
• I want a black background with a very contemporary feel.
• This is a luxury lifestyle product.

```html
<!DOCTYPE html>
<html lang="en">
<head>
<meta charset="utf-8">
<title>Kelvara Pools – Brochure</title>
<link href="https://fonts.googleapis.com/css2?family=Alegreya:wght@400;500&family=Alegreya+Sans:wght@400;500&display=swap" rel="stylesheet">
<style>
  :root{
    --backdrop:#c9b8a4;
    --sheet:#0d0d0e;
    --panel-light:#1a1a1c;
    --panel-dark:#070708;
    --band-top:#0e2a47;
    --band-bottom:#081a2e;
    --accent:#1ea2e4;
    --text:#f2f2f2;
    --photo-frame:#1b4f86;
  }
  *{margin:0;padding:0;box-sizing:border-box}
  html,body{width:1200px;height:1200px;overflow:hidden;background:var(--backdrop)}
  body{position:relative;font-family:"Alegreya",Georgia,serif;color:var(--text);font-variant-numeric:lining-nums}

  .sheet{position:absolute;left:173px;width:853px;background:var(--sheet);display:flex;box-shadow:0 2px 8px rgba(0,0,0,.35)}
  .sheet--inside{top:8px;height:602px}
  .sheet--cover{top:618px;height:582px}

  .panel{position:relative;flex:1;background:linear-gradient(90deg,var(--panel-dark),var(--panel-light) 50%,var(--panel-dark))}
  .panel + .panel{border-left:1px solid #000}

  .photo{position:absolute;left:14px;right:10px;top:17px;height:168px;border:1px solid var(--photo-frame)}
  .photo--garden{background:linear-gradient(180deg,#2a3a2a 0%,#1c2a1c 45%,#2a6fd0 70%,#a8692c 100%)}
  .photo--villa{background:linear-gradient(180deg,#c89a6a 0%,#6e5a44 35%,#1c68b8 65%,#13497f 100%)}
  .photo--firebowl{background:linear-gradient(160deg,#6b6e80 0%,#c07840 40%,#e0882a 55%,#1c4d8a 80%,#b7a690 100%)}

  .heading{position:absolute;left:14px;top:198px;font-family:"Alegreya Sans",Arial,sans-serif;font-weight:500;font-size:20px;color:var(--accent);white-space:nowrap}
  .body-copy{position:absolute;left:18px;right:12px;top:225px;font-size:8px;line-height:14.6px}

  .band{position:absolute;left:0;right:0;bottom:0;height:130px;background:linear-gradient(180deg,var(--band-top),var(--band-bottom))}
  .band__title{position:absolute;left:14px;top:2px;font-size:19px;font-weight:500}
  .band__copy{position:absolute;left:18px;right:4px;top:26px;font-size:7.6px;line-height:14.6px}
  .band__cta{position:absolute;left:73px;top:72px;font-family:"Alegreya Sans",Arial,sans-serif;font-size:13px}

  .contact{position:absolute;left:7px;top:8px;font-size:9.6px;line-height:18.4px}

  .offer__figure{position:absolute;left:6px;top:2px;font-family:"Alegreya Sans",Arial,sans-serif;font-weight:500;font-size:50px;line-height:1}
  .offer__figure small{font-size:9px;margin-left:4px}
  .offer__copy{position:absolute;left:6px;top:56px;font-size:9.6px;line-height:18.4px}

  .brand-name{position:absolute;left:0;right:0;text-align:center;font-family:"Alegreya Sans",Arial,sans-serif;font-weight:400;font-size:28px;letter-spacing:2px;line-height:1;color:var(--text)}
  .brand-name--inside{top:428px}
  .brand-name--cover{top:222px}
</style>
</head>
<body>

<section class="sheet sheet--inside">
  <article class="panel">
    <div class="photo photo--garden" role="img" aria-label="Night-lit backyard pool with palm trees and fire features"></div>
    <h2 class="heading">What do we provide for you</h2>
    <p class="body-copy">Even on the coolest mornings, the stunning outdoor pool in the Aurelian Crest hotel in Marlow Bay is heated to an inviting 28°C. After dark, it takes on a romantic atmosphere – perfect for swimming beneath the stars. The less energetic may prefer to chill out on a sun lounger on the pool deck where members of staff are always on hand to provide shady umbrellas and oversized fluffy towels. With a separate toddler pool and an experienced lifeguard on duty, everyone can enjoy this relaxing outdoor space in the Marlow Bay luxury hotel. The adjoining Grill Bar opens from noon daily during the summer months, serving a wide choice of snacks, beverages and a special Shabbat menu.</p>
    <div class="band">
      <h3 class="band__title">Join our royal family</h3>
      <p class="band__copy">The all-new Halvern Meridian returns as the brand flagship this fall, offering first-class travel for clients in America and abroad through warm, human touches and a contemporary design. The full-size sedan is designed to appeal</p>
      <p class="band__cta">Call now: (231) 555-0148</p>
    </div>
  </article>

  <article class="panel">
    <div class="photo photo--villa" role="img" aria-label="Mediterranean villa at dusk with long blue pool and fire bowl"></div>
    <h2 class="heading" style="top:200px">Join a luxurious lifestyle with us</h2>
    <p class="body-copy" style="left:10px">This exclusive Pickup and Delivery marks another milestone in Halvern Motor Company commitment to merge great products, an outstanding experience and impeccable service – part of its original 2012 business plan. Since Halvern began this journey, it has delivered four all-new products in four years, established a dealer network abroad, built brand awareness, and increased volume for the brand and Halvern products</p>
    <p class="brand-name brand-name--inside">Kelvara</p>
    <div class="band">
      <p class="contact">Address: 8741 Ridgeview Lane<br>Phone: (231) 555-0148<br>Fax: (231) 555-0149<br>Email: hello@kelvarapools.com</p>
    </div>
  </article>

  <article class="panel">
    <div class="photo photo--firebowl" role="img" aria-label="Infinity-edge pool with flaming stone fire bowl at sunset"></div>
    <h2 class="heading" style="top:200px;left:10px">Pools for the mind body&amp;soul</h2>
    <p class="body-copy" style="top:228px;left:8px">“As you settle into relaxation pose, relax the weight of your body into the support of the floor. Notice how the body makes contact with the support of the floor. Relax the back of your legs” the back of your hips” your lower back, middle back and upper back. Relax the back of your shoulders” the back of your arms” the back of your neck” and the back of your head. Make any adjustments you need to, to relax the body into the ground more fully. Relax into the support of floor, completely.</p>
    <div class="band">
      <p class="offer__figure">50%<small>OFF</small></p>
      <p class="offer__copy">A yearly subscribtion if you join our luxurious family<br>until August 2016</p>
    </div>
  </article>
</section>

<section class="sheet sheet--cover">
  <div class="panel"></div>
  <div class="panel">
    <p class="brand-name brand-name--cover">Kelvara</p>
  </div>
  <div class="panel"></div>
</section>

</body>
</html>
```